Website for IT consulting Company

I need a website upgrade, the existing site content is ok, I would also like to add a testimonial page, the site should be something that is easy for us to update content. You use the content from www.kelvanbrook.com as an example. I will also post update logo and artwork. I also need a contact form with some type of validation or captcha.

I added Coded to the Project

Please omit Address maps

Target Market(s)

small business, service oriented companies. We provide IT Consulting, support and mangement

Industry/Entity Type

Information Technology

Coding

Number of Pages Required

1 page

Font styles to use
Serif
Sans Serif

Requirements
Must have
• Contain logo attached, and content from existing web site www.kelvanbrook.com.
• Also need to update content easily, and be movable to different platforms.
• There is a catch phrase
• "Let us worry about your technology…” “ so you don’t have to!”
• Should be included.
Nice to have
• Testimonial page, Project page where we can post new and past projects and pictures
Should not have
• none

```html
<!DOCTYPE html>
<html lang="en">
<head>
<meta charset="utf-8">
<title>Kelvanbrook — IT Consulting</title>
<link href="https://fonts.googleapis.com/css2?family=Roboto+Condensed:wght@700&family=Roboto:wght@400;500;700&family=Lato:wght@400;700&display=swap" rel="stylesheet">
<style>
:root{
  --orange:#f47c20;
  --ink:#111111;
  --dark:#3d3d3d;
  --text:#555555;
  --muted:#8a8a8a;
  --line:#444444;
  --panel:#f0f0f1;
  --white:#ffffff;
}
*{box-sizing:border-box;margin:0;padding:0}
html,body{width:1200px;height:2778px;overflow:hidden}
body{position:relative;background:var(--white);font-family:"Roboto",Arial,sans-serif;color:var(--text)}
a{text-decoration:none}
.abs{position:absolute}

/* header */
.site-header{position:absolute;left:0;top:0;width:1200px;height:111px;background:var(--ink)}
.brand{position:absolute;left:38px;top:18px;display:flex;align-items:center;gap:12px}
.brand-mark{width:40px;height:40px;background:var(--orange)}
.brand-name{font-family:"Roboto",sans-serif;font-weight:700;font-size:34px;color:var(--white);letter-spacing:1px}
.brand-tag{position:absolute;left:90px;top:70px;font-size:10px;color:var(--orange);white-space:nowrap}
.contact-bar{position:absolute;right:26px;top:20px;display:flex;gap:30px;font-size:17px;color:#9a9a9a}
.contact-bar span{display:flex;align-items:center;gap:9px}
.main-nav{position:absolute;right:0;top:57px;display:flex;height:54px}
.main-nav a{display:block;padding:0 16px;line-height:54px;font-size:19px;color:#d6d6d6}
.main-nav a.active{background:var(--orange);color:var(--white);padding:0 20px;margin-right:10px}

/* hero */
.hero{position:absolute;left:0;top:111px;width:1200px;height:589px;background:linear-gradient(90deg,#3a2a20 0%,#5c4536 40%,#8b7767 62%,#5a4a40 100%)}
.hero-photo{position:absolute;inset:0}
.hero-title{position:absolute;left:38px;top:135px;font-family:"Roboto Condensed",sans-serif;font-weight:700;font-size:68px;line-height:76px;color:var(--white)}
.hero-lead{position:absolute;left:38px;top:300px;width:630px;font-family:"Lato",sans-serif;font-size:23px;line-height:35px;color:var(--white)}
.btn{position:absolute;display:block;background:var(--orange);color:var(--white);border-radius:6px;text-align:center;font-family:"Lato",sans-serif;text-decoration:none}
.hero .btn{left:38px;top:403px;width:124px;height:43px;line-height:43px;font-size:18px}

/* section headings */
.sec-title{position:absolute;left:0;width:1200px;text-align:center;font-family:"Roboto",sans-serif;font-weight:700;font-size:32px;color:var(--ink)}
.divider{position:absolute;width:216px;height:14px}
.divider::before{content:"";position:absolute;left:0;right:0;top:6px;height:2px;background:var(--line)}
.divider::after{content:"";position:absolute;left:101px;top:0;width:14px;height:14px;background:var(--ink)}
.divider.light::before{background:#bdbdbd}
.divider.light::after{background:var(--white)}

/* what we do */
.card{position:absolute;top:868px;height:200px;border:2px solid var(--dark);border-radius:10px;background:var(--white)}
.card.featured{border-color:var(--orange)}
.card-icon{position:absolute;left:-2px;top:-48px;width:102px;height:96px;border-radius:12px;background:var(--dark)}
.card.featured .card-icon{background:var(--orange)}
.card-icon svg{position:absolute;left:18px;top:16px}
.card-title{position:absolute;left:140px;top:15px;font-size:19px;line-height:20px;color:var(--ink)}
.card-text{position:absolute;left:50px;right:20px;top:100px;font-size:14px;line-height:25px;color:#444}

/* it support */
.support{position:absolute;left:0;top:1111px;width:1200px;height:530px;background:var(--panel)}
.support-photo{position:absolute;left:0;top:0;width:560px;height:530px;background:linear-gradient(90deg,#3b3a3a 0%,#6a625c 50%,#b5b1ad 80%,var(--panel) 100%)}
.service{position:absolute;width:300px;height:80px}
.service-icon{position:absolute;left:0;top:0;width:72px;height:72px;border:2px solid var(--dark);border-radius:50%;background:var(--white)}
.service-icon svg{position:absolute;left:20px;top:20px}
.service.active .service-icon{background:var(--orange);border-color:var(--orange)}
.service h3{position:absolute;left:90px;top:2px;font-weight:400;font-size:19px;color:#444;white-space:nowrap}
.service.active h3{color:var(--orange)}
.service p{position:absolute;left:90px;top:28px;width:200px;font-size:14px;line-height:20px;color:#555}
.service.right p{width:180px}
.service.faded h3,.service.faded p{color:#8d8d8d}

/* about */
.about-text{position:absolute;left:40px;top:1762px;width:690px;font-size:14.5px;line-height:27px;color:var(--muted)}
.about-text strong{color:#333;font-weight:500}
.about-text p+p{margin-top:10px}
.about .btn{left:40px;top:2040px;width:104px;height:36px;line-height:36px;font-size:14px}
.about-photo{position:absolute;left:713px;top:1690px;width:487px;height:366px;background:linear-gradient(90deg,rgba(255,255,255,1) 0%,#d9d2cc 30%,#8b7a70 60%,#c9c4c0 100%)}

/* testimonials */
.testimonials{position:absolute;left:0;top:2122px;width:1200px;height:656px;background:linear-gradient(180deg,#1b1b1b 0%,#141414 60%,#070707 100%)}
.testimonials .sec-title{color:var(--white);top:42px}
.avatar{position:absolute;left:560px;top:130px;width:80px;height:80px;border-radius:50%;border:3px solid #fff;background:linear-gradient(180deg,#9aa6b4,#3a4350)}
.quote-mark{position:absolute;left:68px;top:240px;font-family:Georgia,serif;font-size:60px;line-height:60px;color:var(--white)}
.quote{position:absolute;left:75px;top:262px;width:1060px;text-align:center;font-family:Arial,sans-serif;font-size:17px;line-height:28px;color:#a8a8a8}
.author{position:absolute;left:0;top:356px;width:1200px;text-align:center;font-family:Arial,sans-serif;font-weight:700;font-size:18px;color:var(--white)}
.author span{color:var(--orange);font-weight:400}
.dots{position:absolute;left:567px;top:402px;display:flex;gap:10px}
.dots i{display:block;width:10px;height:10px;border:1.5px solid var(--orange);transform:rotate(45deg)}

/* footer */
.social{position:absolute;left:492px;top:2640px;display:flex;gap:10px}
.social i{display:block;width:28px;height:28px;background:#5a5a5a}
.social i:first-child{background:var(--orange)}
.footer-nav{position:absolute;left:0;top:2686px;width:1200px;text-align:center;font-size:14px;color:#8a8a8a}
.footer-nav a{color:#8a8a8a}
.footer-nav a.active{color:var(--white)}
.footer-nav .sep{margin:0 8px}
.copyright{position:absolute;left:0;top:2715px;width:1200px;text-align:center;font-size:14px;color:#9a9a9a}
.copyright b{color:var(--white);font-weight:700}
</style>
</head>
<body>

<header class="site-header">
  <div class="brand">
    <div class="brand-mark"></div>
    <div class="brand-name">KELVANBROOK</div>
  </div>
  <div class="brand-tag">Let us worry about your technology… So you don't have to!</div>
  <div class="contact-bar">
    <span><svg width="18" height="14" viewBox="0 0 18 14"><rect x="1" y="1" width="16" height="12" fill="none" stroke="#f47c20" stroke-width="2"/><path d="M1 1l8 7 8-7" fill="none" stroke="#f47c20" stroke-width="2"/></svg>info@kelvanbrook.com</span>
    <span><svg width="18" height="18" viewBox="0 0 18 18"><path d="M4 1l3 4-2 2c1 2 3 4 5 5l2-2 4 3-2 3C8 16 2 10 1 4z" fill="#f47c20"/></svg>+1 555.204.7781</span>
  </div>
  <nav class="main-nav">
    <a class="active" href="#">Home</a><a href="#">About</a><a href="#">Supports</a><a href="#">Clients</a><a href="#">Projects</a><a href="#">Careers</a><a href="#">Contact</a>
  </nav>
</header>

<section class="hero">
  <div class="hero-photo" role="img" aria-label="Photo of a smiling businesswoman working at a laptop in a warm office"></div>
  <h1 class="hero-title">FLEXIBLE SOLUTIONS<br>FOR YOUR BUSINESS</h1>
  <p class="hero-lead">Outsourcing is subcontracting a process, such as product design or manufacturing, to a third-party company.</p>
  <a class="btn" href="#">Read More</a>
</section>

<section class="what-we-do">
  <h2 class="sec-title" style="top:742px">WHAT WE &nbsp;DO</h2>
  <div class="divider" style="left:494px;top:790px"></div>

  <div class="card featured" style="left:37px;width:274px">
    <div class="card-icon"><svg width="66" height="62" viewBox="0 0 66 62"><circle cx="24" cy="26" r="14" fill="none" stroke="#fff" stroke-width="7" stroke-dasharray="6 4"/><circle cx="24" cy="26" r="5" fill="#fff"/><circle cx="50" cy="46" r="8" fill="none" stroke="#fff" stroke-width="5" stroke-dasharray="4 3"/></svg></div>
    <div class="card-title">Managed IT<br>Solutions</div>
    <p class="card-text">Our staff will design, service, administer and maintain your IT needs. We are well versed on all major operating...</p>
  </div>
  <div class="card" style="left:341px;width:248px">
    <div class="card-icon"><svg width="66" height="62" viewBox="0 0 66 62"><circle cx="30" cy="16" r="12" fill="#fff"/><path d="M6 52c0-14 10-22 24-22s24 8 24 22z" fill="#fff"/><rect x="34" y="38" width="26" height="18" fill="#3d3d3d" stroke="#fff" stroke-width="3"/></svg></div>
    <div class="card-title">Remote<br>Diagnostic<br>&amp; Support</div>
    <p class="card-text" style="left:50px">Do you need a quick solution to a technical problem? With our live remote -assistance tool...</p>
  </div>
  <div class="card" style="left:617px;width:246px">
    <div class="card-icon"><svg width="66" height="62" viewBox="0 0 66 62"><rect x="6" y="4" width="30" height="14" rx="2" fill="#fff"/><rect x="6" y="21" width="30" height="14" rx="2" fill="#fff"/><rect x="22" y="28" width="36" height="24" fill="#3d3d3d" stroke="#fff" stroke-width="3"/><rect x="34" y="53" width="12" height="4" fill="#fff"/></svg></div>
    <div class="card-title">Data<br>Center</div>
    <p class="card-text">Lorem ipsum dolor sitet, consectetur adipiscinglit. Quisque pulvinar pretium interdumuisque coallis...</p>
  </div>
  <div class="card" style="left:893px;width:274px">
    <div class="card-icon"><svg width="66" height="62" viewBox="0 0 66 62"><rect x="10" y="24" width="42" height="28" fill="none" stroke="#fff" stroke-width="4"/><rect x="22" y="54" width="18" height="4" fill="#fff"/><path d="M36 4l14 14-18 20-6 2 2-6z" fill="#fff"/></svg></div>
    <div class="card-title">IT<br>Infrastructure<br>Design &amp;<br>Installation</div>
    <p class="card-text" style="left:18px">Do you need a quick solution to a technical problem? With our live remote-assistanc tool, a member of our support....</p>
  </div>
</section>

<section class="support">
  <div class="support-photo" role="img" aria-label="Photo of a man working on a laptop in an office"></div>
  <h2 class="sec-title" style="left:520px;width:600px;top:42px">IT SUPPORT SOLUTIONS</h2>
  <div class="divider" style="left:712px;top:90px"></div>

  <div class="service active" style="left:548px;top:128px">
    <div class="service-icon"><svg width="32" height="32" viewBox="0 0 32 32" fill="#fff"><circle cx="16" cy="16" r="4"/><circle cx="16" cy="4" r="3"/><circle cx="5" cy="24" r="3"/><circle cx="27" cy="24" r="3"/><path d="M16 16V4M16 16L5 24M16 16l11 8" stroke="#fff" stroke-width="2"/></svg></div>
    <h3>Network Adminstration</h3><p>risus nec commodo porttitor, arcu ipsum imperdiet lacus,</p>
  </div>
  <div class="service right" style="left:902px;top:128px">
    <div class="service-icon"><svg width="32" height="32" viewBox="0 0 32 32" fill="none" stroke="#3d3d3d" stroke-width="2.5"><rect x="4" y="5" width="12" height="22"/><rect x="14" y="12" width="14" height="10"/></svg></div>
    <h3>Desktop Support</h3><p>Praesent consecteturant siut neque luctusnec luc</p>
  </div>
  <div class="service" style="left:548px;top:222px">
    <div class="service-icon"><svg width="32" height="32" viewBox="0 0 32 32" fill="none" stroke="#3d3d3d" stroke-width="2.5"><rect x="5" y="14" width="8" height="10" rx="2"/><rect x="19" y="14" width="8" height="10" rx="2"/><path d="M9 14V4M23 14V4M9 24v5M23 24v5"/></svg></div>
    <h3>Netwrok Cabling</h3><p>Asrit consectetur tellus nunc vitae lacusliquam phare</p>
  </div>
  <div class="service right" style="left:902px;top:222px">
    <div class="service-icon"><svg width="32" height="32" viewBox="0 0 32 32" fill="none" stroke="#3d3d3d" stroke-width="2.5"><path d="M3 13a19 19 0 0 1 26 0M7 18a13 13 0 0 1 18 0M11 23a7 7 0 0 1 10 0"/><circle cx="16" cy="27" r="1.5" fill="#3d3d3d"/></svg></div>
    <h3>Wireless Network</h3><p>Tus massa pulvinaraece nasnisl neque elementu</p>
  </div>
  <div class="service" style="left:548px;top:316px">
    <div class="service-icon"><svg width="32" height="32" viewBox="0 0 32 32" fill="#3d3d3d"><rect x="4" y="8" width="6" height="20" rx="2"/><rect x="12" y="10" width="16" height="18" rx="2"/><rect x="15" y="13" width="10" height="4" fill="#fff"/></svg></div>
    <h3>Telecommunications</h3><p>tra nisi enim, vitae interdum nisl euismod euusce utneque</p>
  </div>
  <div class="service right" style="left:902px;top:316px">
    <div class="service-icon"><svg width="32" height="32" viewBox="0 0 32 32"><path d="M16 3l11 4v8c0 8-5 12-11 14C10 27 5 23 5 15V7z" fill="#3d3d3d"/></svg></div>
    <h3>Antivirus Soultions</h3><p>Smet massa euursus vrr ipsum Vivamus vehicula</p>
  </div>
  <div class="service faded" style="left:548px;top:408px">
    <div class="service-icon"><svg width="32" height="32" viewBox="0 0 32 32" fill="none" stroke="#3d3d3d" stroke-width="3"><circle cx="16" cy="16" r="12"/><circle cx="16" cy="16" r="5"/><path d="M8 8l4 4M24 8l-4 4M8 24l4-4M24 24l-4-4"/></svg></div>
    <h3>Disaster Recovery</h3><p>ipsum. Vestibulum a augue nisi. Nulla luctus leo mi,</p>
  </div>
  <div class="service right" style="left:902px;top:408px">
    <div class="service-icon"><svg width="32" height="32" viewBox="0 0 32 32" fill="none" stroke="#3d3d3d" stroke-width="2.5"><rect x="3" y="5" width="26" height="18"/><path d="M11 28h10M16 23v5M7 10h18"/></svg></div>
    <h3>Web Design</h3><p>Bibendum augue ac laci sagittis accums pulvinar</p>
  </div>
</section>

<section class="about">
  <div class="about-photo" role="img" aria-label="Photo of a businesswoman with a cup at a laptop"></div>
  <h2 class="sec-title" style="left:0;width:1190px;top:1682px">ABOUT US</h2>
  <div class="divider" style="left:494px;top:1730px"></div>
  <div class="about-text">
    <p><strong>Outsourcing</strong> is subcontracting a process, such as product design or manufacturing, to a third-party company. The decision to outsource is often made in the interest of lowering firm costs, redirecting or conserving energy directed at the competencies of a particular business, or to make more efficient use of land, labor, capital, (information) technology and resources. &nbsp;&nbsp;Outsourcing became part of the business lexicon during the 1980s.</p>
    <p>Kelvanbrook is a technology solution provider based in Houston, Texas. Our goal is to make technology a non-issue for individuals and small to medium size businesses ranging from 5 to 150 Users. Kelvanbrook has the experience, the tools, high-level technology solutions and training to power your business and your work force. We understand that all business's have one goal in common!</p>
  </div>
  <a class="btn" href="#">Read More</a>
</section>

<section class="testimonials">
  <h2 class="sec-title">TESTIMONIALS</h2>
  <div class="divider light" style="left:494px;top:90px"></div>
  <svg class="abs" style="left:550px;top:120px" width="100" height="125" viewBox="0 0 100 125"><path d="M50 4a46 46 0 0 1 24 85L50 121 26 89A46 46 0 0 1 50 4z" fill="#f47c20"/></svg>
  <div class="avatar" role="img" aria-label="Portrait photo of the client giving the testimonial"></div>
  <div class="quote-mark">“</div>
  <p class="quote">praesent consectetur ante ut neque luctus, nec luctus massa pulvinar. Maecenas nisl neque, elementum et massa eu, cursus viverra ipsum. Vivamus vehicula bibendum augue, ac lacinia mi sagittis accumsan. In pulvinar, risus nec commodo porttitor, arcu ipsum imperdiet lacus, at consectetur tellus nunc</p>
  <div class="author">Lorem ipsum <span>|</span> Company Name</div>
  <div class="dots"><i></i><i></i><i></i><i></i></div>
</section>

<footer>
  <div class="social"><i></i><i></i><i></i><i></i><i></i><i></i></div>
  <div class="footer-nav"><a class="active" href="#">Home</a><span class="sep">/</span><a href="#">About Us</a><span class="sep">/</span><a href="#">Supports</a><span class="sep">/</span><a href="#">Client</a><span class="sep">/</span><a href="#">Careers</a><span class="sep">/</span><a href="#">Contact</a></div>
  <div class="copyright">© 2017. <b>kelvanbrook.</b>All Rights Reserved.</div>
</footer>

</body>
</html>
```